design a construction company business card

Design business card around our logo. Card must have all the typical info: name, title, address, phone, email, business name, etc. Somewhere on the card I would like to see our motto "Solid in Craft... Driven by Dedication." Consider adding a splash of bright orange to the card to complement the blues and silvers/grays in the logo. We are open to metallic inks, textures, etc. We would like to see options on both light and dark backgrounds. The font in the logo is Euro Technic Extended Regular.

```html
<!DOCTYPE html>
<html lang="en">
<head>
<meta charset="utf-8">
<title>Marlow Contracting – Business Card</title>
<link href="https://fonts.googleapis.com/css2?family=Open+Sans:wght@400;600;700&display=swap" rel="stylesheet">
<style>
  :root {
    --page: #f2f2f2;
    --card-dark: #262626;
    --brand-blue: #2169b5;
    --brand-blue-light: #3a86d6;
    --accent-orange: #f07024;
    --text-light: #f4f4f4;
    --text-grey: #9a9a9a;
  }
  * { box-sizing: border-box; margin: 0; padding: 0; }
  html, body {
    width: 1200px; height: 1000px; overflow: hidden;
    background: var(--page);
    font-family: "Open Sans", Arial, sans-serif;
  }
  .card {
    position: absolute;
    width: 560px; height: 320px;
    background: var(--card-dark);
    box-shadow: 0 18px 36px rgba(0,0,0,0.28);
    overflow: hidden;
  }
  .card--front { left: 70px; top: 90px; }
  .card--back  { left: 570px; top: 570px; }

  /* Front */
  .front-brand {
    position: absolute; left: 0; right: 0; top: 110px;
    text-align: center;
  }
  .brand-name {
    display: inline-flex; align-items: center; gap: 10px;
    color: var(--brand-blue-light);
    font-weight: 700; font-size: 30px; letter-spacing: 1px;
  }
  .brand-mark {
    width: 22px; height: 22px; background: var(--brand-blue);
  }
  .brand-sub {
    color: var(--text-grey); font-size: 13px; letter-spacing: 3px;
    margin-top: 6px; text-transform: uppercase;
  }
  .motto {
    color: var(--accent-orange); font-size: 15px; margin-top: 14px;
  }

  /* Back */
  .back-brand {
    position: absolute; left: 34px; top: 118px;
  }
  .back-brand .brand-name { font-size: 24px; }
  .back-brand .brand-sub { font-size: 11px; letter-spacing: 2.5px; }
  .contact {
    position: absolute; left: 318px; top: 38px;
    color: var(--text-light);
  }
  .contact-name {
    font-size: 21px; color: var(--brand-blue-light); letter-spacing: 0.5px;
  }
  .contact-name strong { font-weight: 700; }
  .contact-title { font-size: 12.5px; margin-bottom: 10px; }
  .contact-title span { color: var(--brand-blue-light); }
  .contact-list { list-style: none; }
  .contact-list li {
    display: flex; align-items: center; gap: 9px;
    font-size: 13px; height: 22px;
  }
  .contact-icon {
    width: 18px; height: 18px; border-radius: 50%;
    background: var(--brand-blue);
    display: flex; align-items: center; justify-content: center;
    flex: none;
  }
  .card-wave {
    position: absolute; left: 0; bottom: 0; width: 560px; height: 140px;
  }
  .address {
    position: absolute; right: 30px; bottom: 22px;
    color: var(--text-light); font-size: 13px; font-weight: 600;
  }
</style>
</head>
<body>

  <section class="card card--front" aria-label="Card front">
    <div class="front-brand">
      <div class="brand-name"><span class="brand-mark"></span>MARLOW</div>
      <div class="brand-sub">— Contracting, Inc. —</div>
      <div class="motto">Solid in Craft... Driven by Dedication</div>
    </div>
  </section>

  <section class="card card--back" aria-label="Card back">
    <div class="back-brand">
      <div class="brand-name"><span class="brand-mark"></span>MARLOW</div>
      <div class="brand-sub">— Contracting, Inc. —</div>
    </div>

    <div class="contact">
      <div class="contact-name"><strong>DEAN</strong> HOLLIS</div>
      <div class="contact-title">CEO of <span>Marlow Contracting, INC</span></div>
      <ul class="contact-list">
        <li>
          <span class="contact-icon">
            <svg width="10" height="10" viewBox="0 0 10 10"><path d="M2 1l2 2-1 1.2c.6 1.2 1.6 2.2 2.8 2.8L7 6l2 2-1.2 1.2C4.5 9 1 5.5.8 2.2z" fill="#fff"/></svg>
          </span>(02) 5550 1234
        </li>
        <li>
          <span class="contact-icon">
            <svg width="10" height="10" viewBox="0 0 10 10"><rect x="2.5" y="0.5" width="5" height="9" rx="1" fill="none" stroke="#fff"/><circle cx="5" cy="8" r="0.6" fill="#fff"/></svg>
          </span>0400 555 012
        </li>
        <li>
          <span class="contact-icon">
            <svg width="10" height="10" viewBox="0 0 10 10"><rect x="0.5" y="2" width="9" height="6" fill="#fff"/><path d="M0.5 2l4.5 3.5L9.5 2" fill="none" stroke="#2169b5"/></svg>
          </span>info@marlowbuild.com
        </li>
        <li>
          <span class="contact-icon">
            <svg width="10" height="10" viewBox="0 0 10 10"><circle cx="5" cy="5" r="4.2" fill="none" stroke="#fff"/><ellipse cx="5" cy="5" rx="1.8" ry="4.2" fill="none" stroke="#fff" stroke-width="0.8"/><path d="M0.8 5h8.4" stroke="#fff" stroke-width="0.8"/></svg>
          </span>www.marlowbuild.com
        </li>
      </ul>
    </div>

    <svg class="card-wave" viewBox="0 0 560 140" aria-hidden="true">
      <path d="M0 95 C140 80 260 55 330 20 C250 60 130 85 0 108 Z" fill="var(--accent-orange)"/>
      <path d="M0 118 C200 95 400 55 560 10 L560 140 L0 140 Z" fill="var(--brand-blue)"/>
    </svg>
    <div class="address">18 Example Rd, Northvale NSW 2000</div>
  </section>

</body>
</html>
```